Bramblewick Forage Business Cards

I need a business card with my logo, number, Facebook account, and some information about what I am selling. Green card with logo on the front. 555-214-8392 phone number, @bramblewickforage Facebook, •Orchardgrass Hay •Alfalfa Hay •Mixed Grass Hay , and “Premium Quality Hay” all written on the back.

Target Market(s)

Hay

Contact Information for Business Card

Phone number, Facebook, different types of hay.

Colors
00AB8E
00BBA5
67D7C9
C6EFE9
E9F9F6

```html
<!DOCTYPE html>
<html lang="en">
<head>
<meta charset="utf-8">
<title>Bramblewick Forage Business Cards</title>
<link href="https://fonts.googleapis.com/css2?family=Open+Sans:wght@400;600;700&family=Roboto:wght@700&display=swap" rel="stylesheet">
<style>
  :root {
    --backdrop: #c3c5c7;
    --field-green: #009640;
    --card-white: #ffffff;
    --ink: #1c1c1c;
    --paper-white: #ffffff;
  }
  * { margin: 0; padding: 0; box-sizing: border-box; }
  html, body {
    width: 1187px; height: 1200px; overflow: hidden;
    background: var(--backdrop);
    font-family: "Open Sans", sans-serif;
  }
  .card {
    position: absolute;
    left: 216px;
    width: 756px;
    height: 432px;
    border-radius: 16px;
    overflow: hidden;
  }
  .card-front { top: 122px; background: var(--field-green); }
  .card-back { top: 644px; background: var(--card-white); }

  .front-mark {
    position: absolute; left: 50%; top: 120px;
    width: 110px; height: 110px; margin-left: -55px;
    border-radius: 50%; background: var(--paper-white);
  }
  .front-name {
    position: absolute; left: 0; right: 0; top: 262px;
    text-align: center; color: var(--paper-white);
    font-weight: 700; font-size: 46px; letter-spacing: 0.5px;
  }

  .back-mark {
    position: absolute; left: 180px; top: 114px;
    width: 120px; height: 120px; border-radius: 50%;
    background: var(--field-green);
  }
  .back-info { position: absolute; left: 318px; top: 128px; }
  .back-name { color: var(--ink); font-weight: 700; font-size: 34px; line-height: 1.1; }
  .back-phone {
    margin-top: 22px; font-family: "Roboto", sans-serif; font-weight: 700;
    font-size: 41px; color: var(--ink); line-height: 1;
  }
  .back-social {
    margin-top: 16px; display: flex; align-items: center; gap: 6px;
    font-size: 23px; color: var(--ink); letter-spacing: 0.5px;
  }
  .social-dot { width: 26px; height: 26px; border-radius: 50%; background: var(--field-green); }
  .back-tagline { margin-top: 10px; font-weight: 700; font-size: 19px; color: var(--ink); letter-spacing: 0.5px; }

  .hay-list {
    position: absolute; left: 0; right: 0; top: 350px;
    display: flex; justify-content: center; gap: 14px;
    list-style: none; font-size: 20px; color: var(--ink); letter-spacing: 0.3px;
  }
  .hay-list li { display: flex; align-items: center; gap: 6px; }
  .hay-list li::before {
    content: ""; width: 10px; height: 10px; border-radius: 50%; background: var(--field-green);
  }
  .back-band { position: absolute; left: 0; right: 0; bottom: 0; height: 14px; background: var(--field-green); }
</style>
</head>
<body>
  <section class="card card-front">
    <div class="front-mark"></div>
    <div class="front-name">Bramblewick Forage</div>
  </section>

  <section class="card card-back">
    <div class="back-mark"></div>
    <div class="back-info">
      <div class="back-name">Bramblewick Forage</div>
      <div class="back-phone">555-214-8392</div>
      <div class="back-social"><span class="social-dot"></span>@bramblewickforage</div>
      <div class="back-tagline">“Premium Quality Hay”</div>
    </div>
    <ul class="hay-list">
      <li>Orchardgrass Hay</li>
      <li>Alfalfa Hay</li>
      <li>Mixed Grass Hay</li>
    </ul>
    <div class="back-band"></div>
  </section>
</body>
</html>
```